Website for IT Security Company in Austria with small and medium business customer base

I own a one man IT security company with a customer small to medium business customer base and need a professional looking website that contains the following information:
- Home page: About the company....
- Services: The services that I offer. It would be nice to have icons if possible (e.g Active Directory icon, digital certificate icon, ...) but this is not a must have.
- About me
- Blog: This is not a must have. It would be ok to just link it to an external blog.
- Impressum
- Contact: No form, just telephone number and e-mail address
- Anything else that you think is necessary for a professional appearance
Also I attached the company design. I do have all source files for the logo if required.

Target Market(s)

Small and medium business of all branches located in Austria

Industry/Entity Type

Cyber Security

Coding

Coded - Design and coding required

Number of Pages Required

5+ page

Font styles to use
Serif
Sans Serif
Other font styles liked:
• Bitsumishi, Bankgothic

Colors

Designer to choose only greyscale colors for use in the design.

Requirements
Must have
• The website must be a mobile-first design.
The design should not be too colorful or playful.
The logo should be used as much as possible
Navigation bar with multi drop-down menu for the services that I offer.
Example:
Services
-> Implementations
-> Implementation Service A
-> Implementation Service B
-> Security Audit
-> Audit A
-> Audit B
Maybe you could have service cards that describe the services briefly and on click redirect to the site that describes the service in detail.
End of example
Logo
contact
impressum
services that I offer
about me
about the company
Nice to have
• Icons would be nice (e.g. house for homepage, letter for contact, ...)
Also for the services I offer icons would be nice (Active Directory, digtial certificates, hacking, security auditing)
For the fonts I have only sugested Bitsumishi and Bankgothic as they are part of my logo. No sure if you feel they make sense as part of the website
Should not have
• forms.
I want to the site to be made as easy as possible (HTML5, CSS, javascript/php/.net)
I do not want a wordpress template or suchlike.

```html
<!DOCTYPE html>
<html lang="en">
<head>
<meta charset="utf-8">
<title>Basalt Guard – IT Security</title>
<link rel="stylesheet" href="https://fonts.googleapis.com/css2?family=Orbitron:wght@600;800&family=Michroma&display=swap">
<style>
:root{
  --bg:#0a0a0a;
  --bg-deep:#000;
  --panel:#141414;
  --text:#f2f2f2;
  --muted:#cfcfcf;
  --ring:#f6e9e6;
  --line:#2a2a2a;
}
*{margin:0;padding:0;box-sizing:border-box}
html,body{width:1200px;height:3091px;overflow:hidden;background:var(--bg)}
body{position:relative;font-family:"Michroma",sans-serif;color:var(--text);text-transform:uppercase}
.abs{position:absolute}
.display{font-family:"Orbitron",sans-serif;font-weight:800;letter-spacing:2px}
a{color:inherit;text-decoration:none}

/* header */
.site-header{left:0;top:0;width:1200px;height:160px;background:var(--bg)}
.brand{left:170px;top:96px;width:256px;text-align:center}
.brand-name{font-family:"Orbitron",sans-serif;font-weight:600;font-size:22px;letter-spacing:1px}
.brand-tag{font-size:8px;letter-spacing:9px;margin-top:4px;color:var(--muted)}
.brand-dot{width:40px;height:40px;border-radius:50%;background:var(--text);margin:-70px auto 30px}
.main-nav{left:543px;top:104px;width:484px;display:flex;justify-content:space-between;font-size:8px;letter-spacing:1px;white-space:nowrap}
.search{left:1006px;top:42px}

/* hero */
.hero-photo{left:576px;top:160px;width:460px;height:560px;background:radial-gradient(circle at 64% 62%,#8a8a8a 0,#3a3a3a 22%,#151515 55%,#0a0a0a 100%)}
.hero-title{left:162px;top:350px;width:424px;text-align:center}
.hero-title h1{font-size:38px;letter-spacing:3px;white-space:nowrap}
.hero-title p{font-size:22px;letter-spacing:6px;margin-top:4px}
.btn{display:block;width:180px;height:37px;background:#fff;color:#111;border-radius:5px;font-size:9px;letter-spacing:2px;line-height:37px;text-align:center}
.hero-btn{left:286px;top:451px}
.scroll-down{left:588px;top:592px}
.hero-curve{left:0;top:640px;width:1200px;height:100px}

/* about */
.about{left:0;top:770px;width:1200px;text-align:center}
.about h2{font-size:42px}
.about p{font-size:10.5px;letter-spacing:1.5px;line-height:27px;margin-top:44px;white-space:nowrap}
.about .btn{margin:29px auto 0}

/* services */
.services{left:0;top:1120px;width:1200px;height:553px;background:radial-gradient(ellipse at 50% 30%,#5a5a5a 0,#2c2c2c 40%,#111 100%)}
.services h2{position:absolute;top:96px;width:100%;text-align:center;font-size:34px}
.service{position:absolute;top:236px;width:240px;height:270px;text-align:center}
.service .ring{width:150px;height:150px;border-radius:50%;border:9px solid var(--ring);background:#0b0b0b;margin:0 auto;display:flex;align-items:center;justify-content:center}
.service h3{font-weight:400;font-size:14px;letter-spacing:3px;line-height:28px;margin-top:24px;text-transform:capitalize;font-variant:small-caps}
.service .chev{position:absolute;left:110px;top:254px}

/* blog */
.blog-title{left:0;top:1740px;width:1200px;text-align:center;font-size:32px}
.post{position:absolute;top:1844px;width:277px}
.post .thumb{width:277px;height:178px;background:linear-gradient(160deg,#6a6a6a,#1e1e1e)}
.post h3{font-size:21px;margin-top:26px;letter-spacing:2px;white-space:nowrap}
.post p{font-size:7.5px;line-height:22.5px;margin-top:18px;letter-spacing:.6px;white-space:nowrap}

/* contact */
.contact{left:0;top:2286px;width:1200px;height:480px;background:linear-gradient(90deg,#2a2a2a 0,#161616 45%,#0d0d0d 100%)}
.contact-photo{left:0;top:0;width:486px;height:480px;background:linear-gradient(135deg,#9a9a9a 0,#4a4a4a 40%,#1a1a1a 100%)}
.contact-info{left:733px;top:80px;width:400px}
.contact-info h2{font-size:24px}
.contact-info .label{font-size:13px;letter-spacing:2px;margin:22px 0 0 4px;text-transform:capitalize;font-variant:small-caps}
.row{display:flex;gap:18px;align-items:flex-start;font-size:12px;letter-spacing:2px;margin-left:6px;white-space:nowrap}
.row span{line-height:20px}
.row.addr{margin-top:28px}
.row.phone{margin-top:56px}
.row.mail{margin-top:24px;font-size:10.5px;letter-spacing:1px}

/* footer */
.footer{left:0;top:2766px;width:1200px;height:325px;background:var(--bg-deep)}
.footer .brand{left:150px;top:150px}
.socials{left:174px;top:216px;display:flex;gap:46px}
.socials span{width:16px;height:16px;border-radius:50%;background:var(--text)}
.footer h4{font-size:18px;letter-spacing:1px}
.links{left:465px;top:75px}
.links ul{list-style:none;margin-top:24px}
.links li{font-size:11px;letter-spacing:1.5px;line-height:27px;text-transform:capitalize;font-variant:small-caps}
.links li::before{content:"›";margin-right:14px}
.news{left:744px;top:75px}
.news .field{width:282px;height:46px;background:#fff;color:#666;font-size:9px;letter-spacing:1px;line-height:46px;padding-left:22px;margin-top:26px;text-transform:capitalize}
.news .submit{width:106px;height:48px;background:#2d2d2d;border-radius:5px;font-size:11px;letter-spacing:2px;text-align:center;line-height:48px;margin-top:13px}
.copy{left:753px;top:262px;font-size:8.5px;letter-spacing:1px;display:flex;gap:14px;white-space:nowrap}
.to-top{left:1077px;top:245px}
</style>
</head>
<body>

<header class="site-header abs">
  <div class="brand abs">
    <div class="brand-dot"></div>
    <div class="brand-name">BASALT GUARD</div>
    <div class="brand-tag">IT SECURITY</div>
  </div>
  <nav class="main-nav abs">
    <a href="#">Home</a><a href="#">About me</a><a href="#">Blog</a><a href="#">Services</a><a href="#">Contact</a><a href="#">Imprint</a>
  </nav>
  <svg class="search abs" width="18" height="18" viewBox="0 0 18 18"><circle cx="7" cy="7" r="5" fill="none" stroke="#fff" stroke-width="2.5"/><line x1="11" y1="11" x2="16" y2="16" stroke="#fff" stroke-width="2.5"/></svg>
</header>

<div class="hero-photo abs" role="img" aria-label="Photo of a businessman's hands sheltering a glowing padlock inside a network sphere"></div>
<div class="hero-title abs">
  <h1 class="display">BASALT GUARD</h1>
  <p>IT SECURITY</p>
</div>
<a class="btn hero-btn abs" href="#">Learn more</a>
<svg class="scroll-down abs" width="24" height="14" viewBox="0 0 24 14"><polyline points="3,3 12,11 21,3" fill="none" stroke="#fff" stroke-width="2.5"/></svg>
<svg class="hero-curve abs" viewBox="0 0 1200 100" preserveAspectRatio="none"><path d="M0 10 Q600 140 1200 0 L1200 100 L0 100Z" fill="#0a0a0a"/><path d="M0 10 Q600 140 1200 0" fill="none" stroke="#2e2e2e" stroke-width="3"/></svg>

<section class="about abs">
  <h2 class="display">ABOUT US</h2>
  <p>Cyber security incidents are unfortunately no longer a rarity , but rather<br>commonplace. In many cases, increasing IT security could be quite easy.<br>I am happy to support you with my profound practice and years of experience.</p>
  <a class="btn" href="#">Read more</a>
</section>

<section class="services abs" role="img" aria-label="Background photo of a server room corridor with network lines">
  <h2 class="display">SERVICES</h2>
  <div class="service" style="left:192px">
    <div class="ring"><svg width="64" height="64" viewBox="0 0 64 64" fill="none" stroke="#fff" stroke-width="2.5"><rect x="6" y="24" width="34" height="30"/><rect x="12" y="32" width="10" height="8"/><rect x="26" y="40" width="10" height="8"/><circle cx="46" cy="20" r="8"/><circle cx="46" cy="20" r="3"/></svg></div>
    <h3>Implementations</h3>
    <svg class="chev" width="20" height="12" viewBox="0 0 20 12"><polyline points="2,2 10,10 18,2" fill="none" stroke="#fff" stroke-width="2.5"/></svg>
  </div>
  <div class="service" style="left:480px">
    <div class="ring"><svg width="64" height="64" viewBox="0 0 64 64" fill="none" stroke="#fff" stroke-width="2.5"><path d="M20 28V18a10 10 0 0 1 20 0v10"/><rect x="14" y="28" width="30" height="26" rx="2"/><line x1="29" y1="36" x2="29" y2="46"/><path d="M44 36l10 4v8c0 6-5 9-10 11-5-2-10-5-10-11v-8z" fill="#0b0b0b"/><polyline points="39,46 43,50 49,42"/></svg></div>
    <h3>Security check</h3>
    <svg class="chev" width="20" height="12" viewBox="0 0 20 12"><polyline points="2,2 10,10 18,2" fill="none" stroke="#fff" stroke-width="2.5"/></svg>
  </div>
  <div class="service" style="left:763px">
    <div class="ring"><svg width="64" height="64" viewBox="0 0 64 64" fill="none" stroke="#fff" stroke-width="2.5"><rect x="12" y="14" width="40" height="28" rx="2"/><path d="M6 48h52l-4 6H10z"/><circle cx="32" cy="26" r="6"/><rect x="22" y="34" width="20" height="4"/></svg></div>
    <h3>Security<br>optimization</h3>
    <svg class="chev" width="20" height="12" viewBox="0 0 20 12"><polyline points="2,2 10,10 18,2" fill="none" stroke="#fff" stroke-width="2.5"/></svg>
  </div>
</section>

<h2 class="blog-title abs display">BLOG</h2>
<article class="post" style="left:168px">
  <div class="thumb" role="img" aria-label="Photo of a circuit board with a fingerprint chip"></div>
  <h3 class="display">LORIUM IPSUM</h3>
  <p>Lorem ipsum dolor sit amet,<br>consectetur adipiscing elit, sed do<br>eiusmod tempor incididunt ut labore<br>et dolore.</p>
</article>
<article class="post" style="left:462px">
  <div class="thumb" role="img" aria-label="Photo of an analyst working at monitors in a control room"></div>
  <h3 class="display" style="margin-left:7px">LORIUM IPSUM</h3>
  <p style="margin-left:8px">Lorem ipsum dolor sit amet,<br>consectetur adipiscing elit, sed do<br>eiusmod tempor incididunt ut labore<br>et dolore.</p>
</article>
<article class="post" style="left:755px">
  <div class="thumb" role="img" aria-label="Photo of a technician with a laptop in a server room"></div>
  <h3 class="display" style="margin-left:10px">LORIUM IPSUM</h3>
  <p style="margin-left:4px">Lorem ipsum dolor sit amet,<br>consectetur adipiscing elit, sed do<br>eiusmod tempor incididunt ut labore<br>et dolore.</p>
</article>

<section class="contact abs">
  <div class="contact-photo abs" role="img" aria-label="Photo of an IT specialist standing beside server racks"></div>
  <div class="contact-info abs">
    <h2 class="display">CONTACT US</h2>
    <div class="label">Address</div>
    <div class="row addr"><svg width="14" height="20" viewBox="0 0 14 20"><path d="M7 0a7 7 0 0 0-7 7c0 5 7 13 7 13s7-8 7-13a7 7 0 0 0-7-7z" fill="#fff"/><circle cx="7" cy="7" r="2.5" fill="#1a1a1a"/></svg><span>#123 , Lorium ipsum<br>Dolor amit,<br>NZ: 12345</span></div>
    <div class="row phone"><svg width="16" height="16" viewBox="0 0 16 16"><path d="M3 0l3 4-2 2c1 2 4 5 6 6l2-2 4 3-2 3C7 16 0 9 0 3z" fill="#fff"/></svg><span>555-014-2290</span></div>
    <div class="row mail"><svg width="16" height="12" viewBox="0 0 16 12" fill="none" stroke="#fff" stroke-width="1.6"><rect x="1" y="1" width="14" height="10"/><polyline points="1,1 8,7 15,1"/></svg><span>office@basaltguard.example</span></div>
  </div>
</section>

<footer class="footer abs">
  <div class="brand abs">
    <div class="brand-dot"></div>
    <div class="brand-name">BASALT GUARD</div>
    <div class="brand-tag">IT SECURITY</div>
  </div>
  <div class="socials abs"><span></span><span></span><span></span><span></span></div>
  <div class="links abs">
    <h4 class="display">QUICK LINKS</h4>
    <ul><li>Home</li><li>About Us</li><li>Services</li><li>Blog</li><li>FAQ</li><li>Contact Us</li></ul>
  </div>
  <div class="news abs">
    <h4 class="display">NEWSLETTER</h4>
    <div class="field">Your email (required)</div>
    <div class="submit">Submit</div>
  </div>
  <div class="copy abs"><span>© 2020</span><span>|</span><span>www.basaltguard.example</span></div>
  <svg class="to-top abs" width="12" height="8" viewBox="0 0 12 8"><polyline points="2,6 6,2 10,6" fill="none" stroke="#fff" stroke-width="1.5"/></svg>
</footer>

</body>
</html>
```